Design a large parking banner – mandatory ticket validation in the shop

Banner Size:
548 cm (width) x 154 cm (height)
Note: The banner will be placed in a metal frame at our parking lot entrance, fully visible to every incoming truck driver. The message must be easy to read from a distance.
Goal of the Banner:
To inform all truck drivers that they must validate their entry ticket inside the shop, even if they are parking for a short time.
The message must be displayed in multiple languages for international drivers.
Mandatory Content:
Main message – in multiple languages (clearly separated or stacked):
Dutch (NL): Vergeet je ticket niet te valideren in de shop – verplicht, ook bij kort parkeren!
French (FR): N'oubliez pas de valider votre ticket à la boutique – obligatoire, même pour un court arrêt !
English (EN): Don't forget to validate your entry ticket in the shop – mandatory, even for short stops!
German (DE): Vergessen Sie nicht, Ihr Einfahrticket im Shop zu entwerten – Pflicht, auch bei kurzem Parken!
Polish (PL): Nie zapomnij zatwierdzić biletu w sklepie – obowiązkowe, nawet przy krótkim postoju!
Romanian (RO): Nu uitați să validați biletul în magazin – obligatoriu, chiar și pentru opriri scurte!
You can include more languages if space allows, but these are essential.
Opening Hours Block (in one section below):
Shop Opening Hours
Mon – Fri: 05:30 – 22:00
Sat & Sun: 08:00 – 22:00
Style & Branding:
The design must match the visual identity of Haulport 41Ter
Please refer to the attached photos of existing parking signage for guidance on colors, typography, and layout style
Our logo (attached) must be clearly visible and professionally integrated
Feel free to use icons or pictograms to visually support the message (e.g., ticket, truck, arrow)
Readability is key – large, bold text and high contrast colors that are visible from a distance
Target Audience:
International truck drivers – people who need fast, clear communication. Not everyone speaks the local language, so visual clarity and multilingual messaging are critical.
File Requirements:
Print-ready file (PDF or EPS) – 300 dpi at 1:10 scale
Include 5 cm bleed on all sides
Provide open source files if possible (AI or PSD)

```html
<!DOCTYPE html>
<html lang="en">
<head>
<meta charset="utf-8">
<title>Haulport 41Ter – Parking Ticket Banner</title>
<link rel="stylesheet" href="https://fonts.googleapis.com/css2?family=Roboto+Condensed:wght@400;700;800&display=swap">
<style>
  :root {
    --navy: #1d2146;
    --navy-deep: #161a3a;
    --red: #d0142c;
    --white: #ffffff;
    --parking-blue: #1f6fbf;
    --label-blue: #2a7fd0;
    --page: #e9ecf1;
  }
  * { margin: 0; padding: 0; box-sizing: border-box; }
  html, body {
    width: 1200px; height: 800px; overflow: hidden;
    background: var(--page);
    font-family: "Roboto Condensed", "Arial Narrow", sans-serif;
  }
  .banner {
    position: absolute; left: 30px; top: 240px;
    width: 1140px; height: 320px;
    background: var(--navy);
    color: var(--white);
    overflow: hidden;
  }
  .brand {
    position: absolute; left: 24px; top: 18px;
    font-weight: 800; font-size: 26px; letter-spacing: 0.5px;
    color: var(--white);
  }
  .headline {
    position: absolute; left: 210px; top: 16px; right: 24px;
    font-weight: 700; font-size: 29px; line-height: 1.2;
    text-align: left; white-space: nowrap;
  }
  .header-rule {
    position: absolute; left: 0; right: 0; top: 66px;
    height: 2px; background: var(--red);
  }
  .must-read {
    position: absolute; left: 24px; top: 78px;
    display: flex; align-items: center; gap: 8px;
    font-weight: 700; font-size: 21px;
  }
  .must-read svg { width: 24px; height: 24px; }
  .messages {
    position: absolute; left: 50px; top: 112px;
    list-style: none;
  }
  .messages li {
    display: flex; align-items: baseline;
    font-weight: 700; font-size: 15.5px; line-height: 31px;
    white-space: nowrap;
  }
  .messages .bullet {
    color: var(--red); font-weight: 800; width: 28px; flex: none;
  }
  .info-column {
    position: absolute; right: 22px; top: 82px; width: 210px;
    display: flex; flex-direction: column; align-items: center;
  }
  .parking-sign { width: 76px; height: 96px; }
  .parking-direction {
    margin-top: -8px;
    display: flex; align-items: center; justify-content: center; gap: 6px;
    width: 150px; height: 30px;
    background: var(--white); color: var(--navy-deep);
    border: 2px solid var(--navy-deep);
    font-weight: 700; font-size: 19px;
  }
  .hours-title {
    margin-top: 10px; padding: 3px 8px;
    background: var(--label-blue); border-radius: 3px;
    font-weight: 700; font-size: 17px; color: var(--white);
  }
  .hours-list { list-style: none; margin-top: 6px; text-align: center; }
  .hours-list li {
    font-weight: 700; font-size: 13px; line-height: 20px;
    border-bottom: 2px solid var(--red);
    padding: 2px 4px 0; margin-bottom: 4px;
  }
</style>
</head>
<body>
  <section class="banner">
    <div class="brand">Haulport 41Ter</div>
    <h1 class="headline">"Attention Drivers: Entry Tickets Must Be Verified Inside the Shop."</h1>
    <div class="header-rule"></div>

    <div class="must-read">
      <svg viewBox="0 0 24 24" aria-hidden="true">
        <circle cx="12" cy="12" r="10" fill="none" stroke="#d0142c" stroke-width="2.4"/>
        <rect x="10.6" y="5.5" width="2.8" height="8.5" fill="#ffffff"/>
        <rect x="10.6" y="15.6" width="2.8" height="2.8" fill="#ffffff"/>
      </svg>
      <span>MUST READ!</span>
    </div>

    <ul class="messages">
      <li><span class="bullet">&gt;&gt;</span>English (EN): Don't forget to validate your entry ticket in the shop – mandatory, even for short stops!</li>
      <li><span class="bullet">&gt;&gt;</span>French (FR): N'oubliez pas de valider votre ticket à la boutique – obligatoire, même pour un court arrêt !</li>
      <li><span class="bullet">&gt;&gt;</span>Dutch (NL): Vergeet je ticket niet te valideren in de shop – verplicht, ook bij kort parkeren!</li>
      <li><span class="bullet">&gt;&gt;</span>German (DE): Vergessen Sie nicht, Ihr Einfahrticket im Shop zu entwerten – Pflicht, auch bei kurzem Parken!</li>
      <li><span class="bullet">&gt;&gt;</span>Polish (PL): Nie zapomnij zatwierdzić biletu w sklepie – obowiązkowe, nawet przy krótkim postoju!</li>
      <li><span class="bullet">&gt;&gt;</span>Romanian (RO): Nu uitați să validați biletul în magazin – obligatoriu, chiar și pentru opriri scurte!</li>
    </ul>

    <aside class="info-column">
      <svg class="parking-sign" viewBox="0 0 76 96" role="img" aria-label="Parking sign">
        <rect x="35" y="60" width="6" height="36" fill="#ffffff"/>
        <rect x="3" y="2" width="70" height="70" rx="10" fill="#1f6fbf" stroke="#ffffff" stroke-width="3"/>
        <text x="38" y="58" text-anchor="middle" font-family="Roboto Condensed, sans-serif" font-weight="700" font-size="54" fill="#ffffff">P</text>
      </svg>
      <div class="parking-direction"><span>←</span><span>PARKING</span><span>→</span></div>
      <div class="hours-title">SHOP OPENING HOURS</div>
      <ul class="hours-list">
        <li>MON – FRI: 05:30 – 22:00</li>
        <li>SAT &amp; SUN: 08:00 – 22:00</li>
      </ul>
    </aside>
  </section>
</body>
</html>
```